Weightloss company needs Business Card

We want a business card that is clean and professional, yet portrays that we are a friendly, innovative, and versatile program designed to fit the needs of our clients.
I would like there to be 2 sides, one side having an appointment card, and the other side containing the logo and business information. There can be decorations on both sides. The logo is attached.

Target Market(s)

Men and women 40-60

Industry/Entity Type

Business

Contact Information for Business Card

Font styles to use
Sans Serif

Requirements
Must have
• The logo, space for business information
Nice to have
• The colors in the logo
Should not have
• No pictures of people or food

```html
<!DOCTYPE html>
<html lang="en">
<head>
<meta charset="utf-8">
<title>Renew Turn Wellness – Business Card</title>
<link rel="stylesheet" href="https://fonts.googleapis.com/css2?family=Questrial&display=swap">
<style>
  :root {
    --bg: #e4e5e8;
    --card: #ffffff;
    --red: #e8192c;
    --cyan: #45c3ee;
    --ink: #1d1d1f;
    --rule: #2a2a2a;
  }
  * { margin: 0; padding: 0; box-sizing: border-box; }
  html, body { width: 1200px; height: 900px; overflow: hidden; }
  body {
    background: var(--bg);
    font-family: "Questrial", "Century Gothic", sans-serif;
    color: var(--ink);
    position: relative;
  }
  .card {
    position: absolute;
    width: 600px;
    height: 343px;
    background: var(--card);
    border-radius: 22px;
    box-shadow: 0 10px 30px rgba(0,0,0,.18);
    overflow: hidden;
  }
  .card--appointment { left: 70px; top: 90px; }
  .card--contact { left: 530px; top: 467px; }

  .brand {
    position: absolute;
    display: flex;
    align-items: center;
    gap: 10px;
    color: var(--red);
    font-size: 24px;
    line-height: 1.05;
    text-align: right;
    z-index: 1;
  }
  .brand__dot {
    width: 14px; height: 14px; border-radius: 50%;
    background: var(--red);
    flex: none;
  }
  .card--appointment .brand { right: 40px; top: 46px; }
  .card--contact .brand { right: 40px; top: 78px; }

  .appointment {
    position: absolute;
    left: 44px;
    right: 44px;
    bottom: 42px;
  }
  .appointment__title {
    color: var(--cyan);
    font-size: 15px;
    letter-spacing: .5px;
    margin-bottom: 14px;
  }
  .field {
    display: flex;
    align-items: flex-end;
    gap: 10px;
    font-size: 17px;
    height: 42px;
  }
  .field__label { width: 52px; flex: none; }
  .field__line { flex: 1; border-bottom: 1.5px solid var(--rule); margin-bottom: 4px; }

  .swoosh { position: absolute; inset: 0; }

  .person {
    position: absolute;
    left: 40px;
    top: 126px;
    font-size: 15px;
    line-height: 1.35;
    z-index: 1;
  }
  .person__name {
    color: var(--cyan);
    font-size: 26px;
    letter-spacing: 1px;
    line-height: 1.1;
  }
  .person__role { font-size: 14px; margin-bottom: 10px; }
  .person__address { margin-bottom: 10px; }
  .contact-list { list-style: none; }
  .contact-list li { display: flex; align-items: center; gap: 10px; }
  .contact-list svg { width: 14px; height: 14px; flex: none; }
</style>
</head>
<body>

<section class="card card--appointment">
  <div class="brand"><span class="brand__dot"></span><span>Renew Turn<br>Wellness</span></div>
  <div class="appointment">
    <p class="appointment__title">APPOINTMENT</p>
    <div class="field"><span class="field__label">Name:</span><span class="field__line"></span></div>
    <div class="field"><span class="field__label">Date:</span><span class="field__line"></span></div>
    <div class="field"><span class="field__label">Time:</span><span class="field__line"></span></div>
  </div>
</section>

<section class="card card--contact">
  <svg class="swoosh" viewBox="0 0 600 343" aria-hidden="true">
    <path d="M228 0 C 350 15, 392 150, 350 343" fill="none" stroke="var(--cyan)" stroke-width="10"/>
    <path d="M220 2 C 332 20, 372 150, 333 343" fill="none" stroke="var(--red)" stroke-width="6"/>
  </svg>
  <div class="brand"><span class="brand__dot"></span><span>Renew Turn<br>Wellness</span></div>
  <div class="person">
    <p class="person__name">MARCUS HALE</p>
    <p class="person__role">DIRECTOR</p>
    <p class="person__address">Harbor Lane, 40218<br>Port Elden, Westland</p>
    <ul class="contact-list">
      <li>
        <svg viewBox="0 0 16 16"><path d="M3 1.5l3 .5 1 3-2 1.3a8 8 0 0 0 4.7 4.7L11 9l3 1 .5 3-2 1.5C7 14 2 9 1.5 3.5z" fill="var(--cyan)"/></svg>
        <span>+100 5550-1234</span>
      </li>
      <li>
        <svg viewBox="0 0 16 16"><rect x="1" y="3" width="14" height="10" fill="none" stroke="var(--cyan)" stroke-width="1.5"/><path d="M1 3l7 6 7-6" fill="none" stroke="var(--cyan)" stroke-width="1.5"/></svg>
        <span>info@renewturnwellness.com</span>
      </li>
      <li>
        <svg viewBox="0 0 16 16"><g fill="none" stroke="var(--cyan)" stroke-width="1.3"><circle cx="8" cy="8" r="6.5"/><ellipse cx="8" cy="8" rx="3" ry="6.5"/><path d="M1.5 8h13M2.5 4.8h11M2.5 11.2h11"/></g></svg>
        <span>www.renewturnwellness.com</span>
      </li>
    </ul>
  </div>
</section>

</body>
</html>
```